Re-design and craft the perfect CV platform

We are building a CV-based platform designed to connect employees and employers, with a strong focus on individual users. As we're just starting out, we're looking to have our platform and logo redesigned to better reflect our vision
https://app.zelvorhire.com/
Colors like in the logo attached
#87C032 #6A6E71 #618930 - also you can add more colors if you like.
https://app.zelvorhire.com/dashboard - This page would be nice if you plan it, like personal Bio dashboard. Attached picture (Dashboard wanted) one idea from how we would like to be, but we are open for new professional ideas/solutions.
https://app.zelvorhire.com/posts - On this page we want to be showed the jobs posted. Attached one picture about our idea (jobs page wanted)
https://app.zelvorhire.com/profile - design something nice.
Only Photoshop, Illustrator or Interface Design
Other pictures from the app attached (as looking right now)

Target Market(s)

Job seekers, HR, Recruiters

Industry/Entity Type

HR Tech

Number of Pages Required

5+ page

Colors
00AB8E
00BBA5
67D7C9
C6EFE9
E9F9F6

```html
<!DOCTYPE html>
<html lang="en">
<head>
<meta charset="utf-8">
<title>HIRELUME – Recruitment Web App Screens</title>
<link href="https://fonts.googleapis.com/css2?family=Poppins:wght@300;400;500;600;700&display=swap" rel="stylesheet">
<style>
:root{
  --teal:#00AB8E;
  --teal-2:#00BBA5;
  --teal-3:#67D7C9;
  --teal-4:#C6EFE9;
  --teal-5:#E9F9F6;
  --board:#E4E4E4;
  --frame:#3B3B3B;
  --ink:#2B2E33;
  --muted:#8A8F96;
  --faint:#C2C6CB;
  --line:#E6E8EB;
  --screen:#F5F6F8;
  --white:#FFFFFF;
  --pink:#E9457A;
  --blue:#3B82F6;
}
*{box-sizing:border-box;margin:0;padding:0}
html,body{width:1200px;height:1200px;overflow:hidden}
body{background:var(--board);font-family:'Poppins',sans-serif;color:var(--ink);position:relative}
.abs{position:absolute}
.label{position:absolute;font-size:10px;color:#8C8C8C;font-weight:400;letter-spacing:.2px}
.frame{position:absolute;border:2.5px solid var(--frame);border-radius:4px;background:var(--screen);overflow:hidden}
.toolbar{position:absolute;left:0;top:0;right:0;height:13px;background:var(--frame);display:flex;align-items:center;padding:0 5px;gap:3px}
.dot{width:3.5px;height:3.5px;border-radius:50%}
.dot.r{background:#FF5F57}.dot.y{background:#FEBC2E}.dot.g{background:#28C840}
.toolbar .nav{color:#DADADA;font-size:6px;margin-left:4px;letter-spacing:2px;line-height:1}
.toolbar .spacer{flex:1}
.toolbar svg{display:block}
.screen{position:absolute;left:0;right:0;top:13px;bottom:0;overflow:hidden}
.brand{display:flex;align-items:center;gap:3px;font-weight:600;color:var(--teal);letter-spacing:.3px;white-space:nowrap}
.brand i{display:block;border-radius:50%;background:var(--teal)}
.muted{color:var(--muted)}
.btn{position:absolute;background:var(--teal);color:#fff;border-radius:2px;display:flex;align-items:center;justify-content:space-between;padding:0 5px;font-weight:500;letter-spacing:.2px}
.input{position:absolute;background:#fff;border:1px solid var(--line);border-radius:2px;display:flex;align-items:center;gap:4px;padding:0 5px;color:var(--muted)}
.foot{position:absolute;font-size:3px;color:var(--faint);text-align:center}
.photo{position:absolute}
.appbar{position:absolute;left:0;right:0;top:0;height:27px;background:#fff;border-bottom:1px solid var(--line)}
.pills{position:absolute;top:8px;left:124px;display:flex;gap:3px;border:1px solid var(--line);border-radius:8px;padding:1px}
.pill{font-size:3.2px;color:var(--muted);display:flex;align-items:center;gap:2px;padding:0 5px;height:11px;border-radius:6px;white-space:nowrap}
.pill.on{background:var(--teal);color:#fff}
.pill b{display:block;width:4px;height:4px;border:.6px solid currentColor;border-radius:1px}
.roundicon{position:absolute;top:8px;width:13px;height:13px;border:1px solid var(--line);border-radius:50%;display:flex;align-items:center;justify-content:center}
.userchip{position:absolute;top:7.5px;height:14px;border:1px solid var(--line);border-radius:8px;display:flex;align-items:center;gap:3px;padding:0 4px 0 1.5px;font-size:3.2px;font-weight:500;white-space:nowrap}
.avatar{border-radius:50%;background:linear-gradient(160deg,#9AA6B2,#4A5563)}
.stat{position:absolute;background:#fff;border-radius:3px;width:94px;height:53px}
.stat .ic{position:absolute;left:6px;top:6px;width:13px;height:13px;border-radius:50%}
.stat .num{position:absolute;left:5px;top:27px;font-size:10px;font-weight:400}
.stat .cap{position:absolute;left:5px;top:43px;font-size:3.2px;color:var(--muted)}
.stat svg{position:absolute;left:27px;top:25px}
.step{position:absolute;left:10px;display:flex;gap:7px;align-items:center}
.step .c{width:12px;height:12px;border-radius:50%;border:1px solid var(--line);background:#fff}
.step.on .c{background:var(--teal);border-color:var(--teal)}
.step small{display:block;font-size:2.6px;color:var(--faint)}
.step span{display:block;font-size:3.3px;color:var(--ink)}
.field{position:absolute;height:16px;border:1px solid var(--line);border-radius:2px;background:#fff;padding:2px 0 0 19px}
.field::before{content:"";position:absolute;left:6px;top:5px;width:5px;height:5px;border:.6px solid var(--faint);border-radius:1px}
.field small{display:block;font-size:2.4px;color:var(--faint)}
.field span{display:block;font-size:3.6px}
.job{position:absolute;width:73px;height:75px;background:#fff;border:1px solid var(--line);border-radius:3px}
.job.hot{background:var(--teal-5);border-color:var(--teal-5)}
.job .logo{position:absolute;left:5px;top:5px;width:14px;height:14px;border-radius:50%}
.job .mark{position:absolute;right:6px;top:7px;width:7px;height:7px;border-radius:50%;border:.6px solid var(--teal-3)}
.job .mark.fill{background:var(--teal);border-color:var(--teal)}
.job .co{position:absolute;left:5px;top:24px;font-size:2.8px;color:var(--muted)}
.job .ti{position:absolute;left:5px;top:32px;font-size:3.6px;font-weight:500;white-space:nowrap}
.job .pay{position:absolute;left:5px;top:41px;font-size:3.3px;color:var(--teal);white-space:nowrap}
.job .loc{position:absolute;left:5px;top:50px;font-size:2.9px;color:var(--muted);white-space:nowrap}
.job .go{position:absolute;left:5px;right:5px;top:60px;height:10px;border:1px solid var(--line);border-radius:2px;font-size:3px;color:var(--muted);display:flex;align-items:center;justify-content:center;background:#fff}
.job.hot .go{background:var(--teal);border-color:var(--teal);color:#fff}
.side-f{position:absolute;left:6px;width:60px;height:16px;background:#fff;border-radius:2px;padding:2px 4px}
.side-f small{display:block;font-size:2.4px;color:var(--faint)}
.side-f span{display:block;font-size:3.4px}
.bar{position:absolute;left:4px;right:8px;bottom:4px;height:1px;background:var(--line)}
.bar i{display:block;height:100%}
.otp{position:absolute;display:flex;border:1px solid var(--line);border-radius:2px;background:#fff}
.otp span{flex:1;text-align:center;font-size:5px;line-height:16px;border-right:1px solid var(--line)}
.otp span:last-child{border-right:0}
.otpc{position:absolute;width:14px;height:14px;border-radius:50%;border:1px solid var(--line);background:#fff;font-size:4px;text-align:center;line-height:12px}
.otpc.on{background:var(--teal-4);border-color:var(--teal-3)}
.caption{position:absolute;color:#fff}
.caption h4{font-size:5px;font-weight:600;border-left:1px solid var(--teal-3);padding-left:3px}
.caption p{font-size:3.2px;line-height:1.8;margin-top:4px;opacity:.9}
.caption .pg{display:flex;gap:3px;margin-top:5px}
.caption .pg i{width:2.5px;height:2.5px;border-radius:50%;border:.5px solid #fff}
.caption .pg i:first-child{background:var(--teal-2);border-color:var(--teal-2)}
.quotecard{position:absolute;background:var(--teal);border-radius:3px;color:#fff;text-align:center;padding:8px 4px 0}
.quotecard .q{width:18px;height:18px;border-radius:50%;background:#fff;color:var(--teal);font-size:14px;font-weight:700;line-height:22px;margin:0 auto}
.quotecard h5{font-size:4.6px;font-weight:600;margin-top:6px}
.quotecard p{font-size:3px;line-height:1.8;margin-top:4px}
.thanks{position:absolute;left:0;right:0;top:1145px;text-align:center;font-size:25px;font-weight:700;color:#B5B5B5;letter-spacing:.5px;text-shadow:0 1px 0 #fff,0 -1px 0 rgba(0,0,0,.08)}
</style>
</head>
<body>

<div class="label" style="left:29px;top:41px">01. Email Login</div>
<div class="label" style="left:424px;top:41px">02. One Time Password</div>
<div class="label" style="left:817px;top:41px">03. Dashboard</div>
<div class="label" style="left:29px;top:361px">04. Profile</div>
<div class="label" style="left:424px;top:361px">05. Job</div>
<div class="label" style="left:821px;top:368px">06. Email Login – Option one</div>
<div class="label" style="left:25px;top:812px">07.One Time Password – Option One</div>
<div class="label" style="left:419px;top:812px">08.Email – Option Two</div>
<div class="label" style="left:812px;top:812px">09.One Time Password – Option Two</div>

<!-- 01 Email Login -->
<section class="frame" style="left:24px;top:65px;width:363px;height:257px">
  <div class="toolbar"><i class="dot r"></i><i class="dot y"></i><i class="dot g"></i><span class="nav">‹ › ↻</span><svg width="6" height="6" viewBox="0 0 6 6"><circle cx="2.5" cy="2.5" r="1.8" fill="none" stroke="#ddd" stroke-width=".7"/><path d="M4 4l1.6 1.6" stroke="#ddd" stroke-width=".7"/></svg><span class="spacer"></span><span class="nav">☆ ≡</span></div>
  <div class="screen">
    <svg class="photo" role="img" aria-label="Photo of a team meeting around a table" width="358" height="105" viewBox="0 0 358 105" style="left:0;top:0"><defs><linearGradient id="g1" x1="0" x2="1"><stop offset="0" stop-color="#5E5146"/><stop offset=".5" stop-color="#3C3936"/><stop offset="1" stop-color="#2A2C30"/></linearGradient></defs><path d="M0 0H358V86C300 92 250 70 180 70S60 100 0 88Z" fill="url(#g1)"/></svg>
    <div class="abs" style="left:113px;top:70px;width:134px;height:105px;background:#fff;border-radius:2px">
      <div class="brand" style="position:absolute;left:0;right:0;top:12px;justify-content:center;font-size:9px"><i style="width:8px;height:8px"></i>HIRELUME</div>
      <div class="abs" style="left:0;right:0;top:40px;text-align:center;font-size:4.2px;font-weight:500">Recruitment Web App Access</div>
      <div class="input" style="left:13px;right:13px;top:54px;height:14px;font-size:3.6px"><svg width="6" height="5"><rect x=".5" y=".5" width="5" height="4" fill="none" stroke="#C2C6CB" stroke-width=".6"/></svg>alex.marren@mailbox.test<span style="flex:1"></span><i style="width:4px;height:4px;border-radius:50%;background:var(--teal)"></i></div>
      <div class="btn" style="left:13px;right:13px;top:75px;height:14px;font-size:3.6px"><span>CONTINUE</span><span>»</span></div>
    </div>
    <div class="foot" style="left:0;right:0;top:190px">© 2024 HIRELUME. All rights reserved</div>
  </div>
</section>

<!-- 02 One Time Password -->
<section class="frame" style="left:419px;top:65px;width:363px;height:257px">
  <div class="toolbar"><i class="dot r"></i><i class="dot y"></i><i class="dot g"></i><span class="nav">‹ › ↻</span><svg width="6" height="6" viewBox="0 0 6 6"><circle cx="2.5" cy="2.5" r="1.8" fill="none" stroke="#ddd" stroke-width=".7"/><path d="M4 4l1.6 1.6" stroke="#ddd" stroke-width=".7"/></svg><span class="spacer"></span><span class="nav">☆ ≡</span></div>
  <div class="screen">
    <svg class="photo" role="img" aria-label="Photo of a team meeting around a table" width="358" height="105" viewBox="0 0 358 105" style="left:0;top:0"><defs><linearGradient id="g2" x1="0" x2="1"><stop offset="0" stop-color="#5E5146"/><stop offset=".5" stop-color="#3C3936"/><stop offset="1" stop-color="#2A2C30"/></linearGradient></defs><path d="M0 0H358V86C300 92 250 70 180 70S60 100 0 88Z" fill="url(#g2)"/></svg>
    <div class="abs" style="left:113px;top:70px;width:134px;height:105px;background:#fff;border-radius:2px">
      <div class="brand" style="position:absolute;left:0;right:0;top:12px;justify-content:center;font-size:9px"><i style="width:8px;height:8px"></i>HIRELUME</div>
      <div class="abs" style="left:0;right:0;top:40px;text-align:center;font-size:4.2px;font-weight:500">Recruitment Web App Access</div>
      <div class="input" style="left:13px;right:13px;top:54px;height:14px;font-size:3.6px"><svg width="6" height="5"><rect x=".5" y=".5" width="5" height="4" fill="none" stroke="#C2C6CB" stroke-width=".6"/></svg>alex.marren@mailbox.test<span style="flex:1"></span><i style="width:4px;height:4px;border-radius:50%;background:var(--teal)"></i></div>
      <div class="btn" style="left:13px;right:13px;top:75px;height:14px;font-size:3.6px"><span>CONTINUE</span><span>»</span></div>
    </div>
    <div class="foot" style="left:0;right:0;top:190px">© 2024 HIRELUME. All rights reserved</div>
  </div>
</section>

<!-- 03 Dashboard -->
<section class="frame" style="left:812px;top:65px;width:363px;height:257px">
  <div class="toolbar"><i class="dot r"></i><i class="dot y"></i><i class="dot g"></i><span class="nav">‹ › ↻</span><svg width="6" height="6" viewBox="0 0 6 6"><circle cx="2.5" cy="2.5" r="1.8" fill="none" stroke="#ddd" stroke-width=".7"/><path d="M4 4l1.6 1.6" stroke="#ddd" stroke-width=".7"/></svg><span class="spacer"></span><span class="nav">☆ ≡</span></div>
  <div class="screen">
    <header class="appbar">
      <div class="brand" style="position:absolute;left:12px;top:10px;font-size:5px"><i style="width:5px;height:5px"></i>HIRELUME</div>
      <nav class="pills"><span class="pill on"><b></b>Dashboard</span><span class="pill"><b></b>Profile</span><span class="pill"><b></b>Job Posts</span></nav>
      <div class="roundicon" style="left:270px"><svg width="5" height="5"><circle cx="2" cy="2" r="1.5" fill="none" stroke="#8A8F96" stroke-width=".5"/></svg></div>
      <div class="roundicon" style="left:289px"><i style="width:4px;height:4px;border-radius:50%;border:.7px solid var(--teal)"></i></div>
      <div class="userchip" style="left:307px"><i class="avatar" style="width:11px;height:11px" role="img" aria-label="User avatar"></i>Alex Marren ⌄</div>
    </header>
    <i class="avatar abs" style="left:13px;top:35px;width:16px;height:16px" role="img" aria-label="User avatar"></i>
    <div class="abs" style="left:35px;top:35px;font-size:6.5px">Hello, Alex Marren!</div>
    <div class="abs muted" style="left:35px;top:45px;font-size:3px">Here's an overview of your dashboard</div>
    <div class="stat" style="left:12px;top:65px">
      <i class="ic" style="background:var(--teal)"></i>
      <div class="num">40</div>
      <svg width="64" height="14" viewBox="0 0 64 14"><polyline points="0,12 5,10 9,11 13,6 17,9 21,4 25,10 29,2 33,12 37,5 41,8 45,3 49,11 53,9 57,12 64,11" fill="none" stroke="var(--teal)" stroke-width=".7"/></svg>
      <div class="cap">Total times your CV was purchased</div>
    </div>
    <div class="stat" style="left:113px;top:65px">
      <i class="ic" style="background:var(--blue)"></i>
      <div class="num">120</div>
      <svg width="64" height="14" viewBox="0 0 64 14"><polyline points="0,11 4,8 8,12 12,3 16,10 20,6 24,12 28,4 32,9 36,2 40,12 44,5 48,11 52,3 56,10 60,4 64,9" fill="none" stroke="var(--blue)" stroke-width=".7"/></svg>
      <div class="cap">Total applications sent</div>
    </div>
  </div>
</section>

<!-- 04 Profile -->
<section class="frame" style="left:24px;top:384px;width:363px;height:286px">
  <div class="toolbar"><i class="dot r"></i><i class="dot y"></i><i class="dot g"></i><span class="nav">‹ › ↻</span><svg width="6" height="6" viewBox="0 0 6 6"><circle cx="2.5" cy="2.5" r="1.8" fill="none" stroke="#ddd" stroke-width=".7"/><path d="M4 4l1.6 1.6" stroke="#ddd" stroke-width=".7"/></svg><span class="spacer"></span><span class="nav">☆ ≡</span></div>
  <div class="screen">
    <header class="appbar">
      <div class="brand" style="position:absolute;left:10px;top:10px;font-size:5px"><i style="width:5px;height:5px"></i>HIRELUME</div>
      <nav class="pills" style="left:124px"><span class="pill"><b></b>Dashboard</span><span class="pill on"><b></b>Profile</span><span class="pill"><b></b>Job Posts</span></nav>
      <div class="roundicon" style="left:270px"><svg width="5" height="5"><circle cx="2" cy="2" r="1.5" fill="none" stroke="#8A8F96" stroke-width=".5"/></svg></div>
      <div class="roundicon" style="left:289px"><i style="width:4px;height:4px;border-radius:50%;border:.7px solid var(--teal)"></i></div>
      <div class="userchip" style="left:307px"><i class="avatar" style="width:11px;height:11px" role="img" aria-label="User avatar"></i>Alex Marren ⌄</div>
    </header>
    <i class="avatar abs" style="left:11px;top:37px;width:16px;height:16px" role="img" aria-label="User avatar"></i>
    <div class="abs" style="left:34px;top:37px;font-size:6.5px">Setup Your Profile</div>
    <div class="abs muted" style="left:34px;top:47px;font-size:3px">Build your cv in six easy steps</div>
    <div class="abs" style="left:12px;top:64px;width:341px;height:193px;background:#fff;border-radius:3px">
      <div class="abs" style="left:5px;top:5px;width:80px;height:183px;background:var(--screen);border-radius:3px">
        <i class="abs" style="left:15.5px;top:22px;width:1px;height:10px;background:var(--teal)"></i>
        <div class="step on" style="top:12px"><i class="c"></i><div><small>Step 1</small><span>Personal Details</span></div></div>
        <div class="step" style="top:36px"><i class="c"></i><div><small>Step 2</small><span>Bio</span></div></div>
        <div class="step" style="top:61px"><i class="c"></i><div><small>Step 3</small><span>Work Experience</span></div></div>
        <div class="step" style="top:87px"><i class="c"></i><div><small>Step 4</small><span>Education</span></div></div>
        <div class="step" style="top:111px"><i class="c"></i><div><small>Step 5</small><span>Skills</span></div></div>
        <div class="step" style="top:137px"><i class="c"></i><div><small>Step 6</small><span>Preferences</span></div></div>
        <div class="step" style="top:164px"><i class="c"></i><div><small>Step 7</small><span>Done</span></div></div>
      </div>
      <div class="abs" style="left:102px;top:13px;font-size:4.2px">Personal Details</div>
      <div class="field" style="left:102px;top:24px;width:220px"><small>Upload Profile Picture</small><span>profile.jpeg</span><i class="abs" style="right:2px;top:2px;width:12px;height:11px;background:var(--teal);border-radius:2px"></i></div>
      <div class="field" style="left:102px;top:48px;width:106px"><small>Name</small><span>Alex Marren</span></div>
      <div class="field" style="left:218px;top:48px;width:105px"><small>Email Address</small><span>alex.marren@mailbox.test</span></div>
      <div class="field" style="left:102px;top:70px;width:106px"><small>Phone number</small><span>+1 555 0142 7730</span></div>
      <div class="field" style="left:218px;top:70px;width:105px"><small>Date of Birth</small><span>10 April 1988</span></div>
      <div class="field" style="left:102px;top:94px;width:106px"><small>Address</small><span>48 Linden Lane</span></div>
      <div class="field" style="left:218px;top:94px;width:105px"><small>City</small><span>New York</span></div>
      <div class="field" style="left:102px;top:117px;width:106px"><small>State</small><span>State</span></div>
      <div class="field" style="left:218px;top:117px;width:105px"><small>Post Code</small><span>635 985</span></div>
      <div class="field" style="left:102px;top:138px;width:106px"><small>Country</small><span>USA</span></div>
      <div class="btn" style="left:218px;top:138px;width:105px;height:16px;font-size:3.8px"><span>CONTINUE</span><span>»</span></div>
    </div>
  </div>
</section>

<!-- 05 Job -->
<section class="frame" style="left:419px;top:384px;width:363px;height:377px">
  <div class="toolbar"><i class="dot r"></i><i class="dot y"></i><i class="dot g"></i><span class="nav">‹ › ↻</span><svg width="6" height="6" viewBox="0 0 6 6"><circle cx="2.5" cy="2.5" r="1.8" fill="none" stroke="#ddd" stroke-width=".7"/><path d="M4 4l1.6 1.6" stroke="#ddd" stroke-width=".7"/></svg><span class="spacer"></span><span class="nav">☆ ≡</span></div>
  <div class="screen">
    <header class="appbar">
      <div class="brand" style="position:absolute;left:10px;top:10px;font-size:5px"><i style="width:5px;height:5px"></i>HIRELUME</div>
      <nav class="pills" style="left:124px"><span class="pill"><b></b>Dashboard</span><span class="pill"><b></b>Profile</span><span class="pill on"><b></b>Job Posts</span></nav>
      <div class="roundicon" style="left:270px"><svg width="5" height="5"><circle cx="2" cy="2" r="1.5" fill="none" stroke="#8A8F96" stroke-width=".5"/></svg></div>
      <div class="roundicon" style="left:289px"><i style="width:4px;height:4px;border-radius:50%;border:.7px solid var(--teal)"></i></div>
      <div class="userchip" style="left:307px"><i class="avatar" style="width:11px;height:11px" role="img" aria-label="User avatar"></i>Alex Marren ⌄</div>
    </header>
    <i class="avatar abs" style="left:10px;top:37px;width:16px;height:16px" role="img" aria-label="User avatar"></i>
    <div class="abs" style="left:32px;top:37px;font-size:6.5px">Showing 246 Jobs Results</div>
    <div class="abs muted" style="left:32px;top:47px;font-size:3px">Based your preferences</div>
    <div class="abs" style="left:10px;top:64px;width:340px;height:287px;background:#fff;border-radius:3px">
      <div class="abs" style="left:10px;top:12px;width:72px;height:246px;background:var(--screen);border-radius:3px;overflow:hidden">
        <div class="abs" style="left:0;right:0;top:0;height:27px;background:var(--teal-2)"></div>
        <i class="avatar abs" style="left:20px;top:10px;width:32px;height:32px;border:2px solid #fff" role="img" aria-label="Profile photo"></i>
        <div class="abs" style="left:6px;top:48px;font-size:3.6px">Personal Details</div>
        <div class="side-f" style="top:57px"><small>Name</small><span>Alex Marren</span></div>
        <div class="side-f" style="top:76px"><small>Sex</small><span>Male</span></div>
        <div class="side-f" style="top:96px"><small>Age</small><span>33year 56 days</span></div>
        <div class="side-f" style="top:115px"><small>Highest level study</small><span>MBA</span></div>
        <div class="abs" style="left:6px;top:139px;font-size:3.4px">Skills</div>
        <div class="side-f" style="top:148px"><small>Interface Design</small><div class="bar"><i style="width:88%;background:var(--teal)"></i></div></div>
        <div class="side-f" style="top:168px"><small>Prototyping</small><div class="bar"><i style="width:60%;background:var(--pink)"></i></div></div>
        <div class="abs" style="left:6px;top:191px;font-size:3.4px">Driver License</div>
        <div class="abs" style="left:6px;top:200px;width:60px;height:38px;background:#fff;border-radius:2px;padding:4px">
          <div role="img" aria-label="Scanned driver license card" style="width:100%;height:100%;border-radius:2px;background:linear-gradient(180deg,#2F6FD6 0 18%,#E8EEF6 18% 100%)"></div>
        </div>
      </div>
      <article class="job hot" style="left:93px;top:12px"><i class="logo" style="background:#1F2A5A"></i><i class="mark"></i><div class="co">Norvale Crew Ltd.</div><div class="ti">Backend Programmer</div><div class="pay">▭ $14,000 – $25,000</div><div class="loc">⌖ West Africa, Jordan</div><div class="go">View More / Apply</div></article>
      <article class="job" style="left:175px;top:12px"><i class="logo" style="background:#1B2E6E"></i><i class="mark fill"></i><div class="co">Norvale Crew Ltd.</div><div class="ti">Human Resources Consultant</div><div class="pay">▭ $6000–$12000</div><div class="loc">⌖ West Africa, Jordan</div><div class="go">View More / Apply</div></article>
      <article class="job" style="left:257px;top:12px"><i class="logo" style="background:#3D2A8C"></i><i class="mark"></i><div class="co">Norvale Crew Ltd.</div><div class="ti">Content Writer</div><div class="pay">▭ $9,000 – $15,000</div><div class="loc">⌖ West Africa, Jordan</div><div class="go">View More / Apply</div></article>
      <article class="job" style="left:93px;top:96px"><i class="logo" style="background:#E6E6E6"></i><i class="mark"></i><div class="co">Norvale Crew Ltd.</div><div class="ti">UI UX Designer</div><div class="pay">▭ $14,000 – $25,000</div><div class="loc">⌖ West Africa, Jordan</div><div class="go">View More / Apply</div></article>
      <article class="job" style="left:175px;top:96px"><i class="logo" style="background:#3A3222"></i><i class="mark"></i><div class="co">Norvale Crew Ltd.</div><div class="ti">Front End Developer</div><div class="pay">▭ $6000–$12000</div><div class="loc">⌖ West Africa, Jordan</div><div class="go">View More / Apply</div></article>
      <article class="job" style="left:257px;top:96px"><i class="logo" style="background:#F3D9C2"></i><i class="mark"></i><div class="co">Norvale Crew Ltd.</div><div class="ti">Certified Civil Engineer</div><div class="pay">▭ $9,000 – $15,000</div><div class="loc">⌖ West Africa, Jordan</div><div class="go">View More / Apply</div></article>
      <article class="job" style="left:93px;top:183px"><i class="logo" style="background:#EDE7E7"></i><i class="mark"></i><div class="co">Norvale Crew Ltd.</div><div class="ti">Backend Programmer</div><div class="pay">▭ $14,000 – $25,000</div><div class="loc">⌖ West Africa, Jordan</div><div class="go">View More / Apply</div></article>
      <article class="job" style="left:175px;top:183px"><i class="logo" style="background:#E9E4F5"></i><i class="mark"></i><div class="co">Norvale Crew Ltd.</div><div class="ti">Human Resources Consultant</div><div class="pay">▭ $6000–$12000</div><div class="loc">⌖ West Africa, Jordan</div><div class="go">View More / Apply</div></article>
      <article class="job" style="left:257px;top:183px"><i class="logo" style="background:#4A3B2E"></i><i class="mark"></i><div class="co">Norvale Crew Ltd.</div><div class="ti">Content Writer</div><div class="pay">▭ $9,000 – $15,000</div><div class="loc">⌖ West Africa, Jordan</div><div class="go">View More / Apply</div></article>
      <div class="abs" style="left:155px;top:270px;display:flex;gap:5px">
        <i style="width:7px;height:7px;border-radius:50%;border:.6px solid var(--line);font-size:3px;font-style:normal;text-align:center;line-height:6px;color:var(--muted)">1</i>
        <i style="width:7px;height:7px;border-radius:50%;background:var(--teal);font-size:3px;font-style:normal;text-align:center;line-height:7px;color:#fff">2</i>
        <i style="width:7px;height:7px;border-radius:50%;border:.6px solid var(--line);font-size:3px;font-style:normal;text-align:center;line-height:6px;color:var(--muted)">3</i>
      </div>
    </div>
  </div>
</section>

<!-- 06 Email Login – Option one -->
<section class="frame" style="left:815px;top:391px;width:363px;height:257px">
  <div class="toolbar"><i class="dot r"></i><i class="dot y"></i><i class="dot g"></i><span class="nav">‹ › ↻</span><svg width="6" height="6" viewBox="0 0 6 6"><circle cx="2.5" cy="2.5" r="1.8" fill="none" stroke="#ddd" stroke-width=".7"/><path d="M4 4l1.6 1.6" stroke="#ddd" stroke-width=".7"/></svg><span class="spacer"></span><span class="nav">☆ ≡</span></div>
  <div class="screen" style="background:#fff">
    <div class="photo" role="img" aria-label="Photo of colleagues in an interview at an office table" style="left:2px;top:0;width:185px;bottom:2px;background:linear-gradient(160deg,#DCE3DA 0%,#A7A592 40%,#6F6A5C 75%,#3E3C38 100%)"></div>
    <div class="caption" style="left:20px;top:195px;width:150px"><h4>Perfect CV platform</h4><p>Create, manage, and showcase your professional profile to land your dream job. Easy. Efficient. Effective.</p><div class="pg"><i></i><i></i><i></i></div></div>
    <div class="brand" style="position:absolute;left:188px;right:0;top:70px;justify-content:center;font-size:14px"><i style="width:12px;height:12px"></i>HIRELUME</div>
    <div class="abs" style="left:188px;right:0;top:100px;text-align:center;font-size:4.2px;font-weight:500">Recruitment Web App Access</div>
    <div class="input" style="left:225px;width:108px;top:113px;height:17px;font-size:3.6px;background:var(--screen);flex-direction:column;align-items:flex-start;justify-content:center;gap:1px;color:var(--ink)"><small style="font-size:2.4px;color:var(--faint)">Email Address</small>alex.marren@mailbox.test</div>
    <div class="btn" style="left:225px;width:108px;top:134px;height:17px;font-size:3.6px"><span>CONTINUE</span><span>»</span></div>
    <div class="foot" style="left:188px;right:0;top:233px">© 2024 HIRELUME. All rights reserved</div>
  </div>
</section>

<!-- 07 One Time Password – Option One -->
<section class="frame" style="left:20px;top:836px;width:363px;height:257px">
  <div class="toolbar"><i class="dot r"></i><i class="dot y"></i><i class="dot g"></i><span class="nav">‹ › ↻</span><svg width="6" height="6" viewBox="0 0 6 6"><circle cx="2.5" cy="2.5" r="1.8" fill="none" stroke="#ddd" stroke-width=".7"/><path d="M4 4l1.6 1.6" stroke="#ddd" stroke-width=".7"/></svg><span class="spacer"></span><span class="nav">☆ ≡</span></div>
  <div class="screen" style="background:#fff">
    <div class="photo" role="img" aria-label="Photo of colleagues in an interview at an office table" style="left:2px;top:0;width:182px;bottom:2px;background:linear-gradient(160deg,#DCE3DA 0%,#A7A592 40%,#6F6A5C 75%,#3E3C38 100%)"></div>
    <div class="caption" style="left:17px;top:195px;width:150px"><h4>Perfect CV platform</h4><p>Create, manage, and showcase your professional profile to land your dream job. Easy. Efficient. Effective.</p><div class="pg"><i></i><i></i><i></i></div></div>
    <div class="abs muted" style="left:193px;top:5px;font-size:3.4px">← Back</div>
    <div class="brand" style="position:absolute;left:185px;right:0;top:70px;justify-content:center;font-size:14px"><i style="width:12px;height:12px"></i>HIRELUME</div>
    <div class="abs" style="left:185px;right:0;top:100px;text-align:center;font-size:4.2px;font-weight:500">A one-time password has been sent to you</div>
    <div class="otp" style="left:222px;width:108px;top:113px;height:17px"><span>8</span><span>0</span><span>3</span><span>5</span><span></span><span></span></div>
    <div class="btn" style="left:222px;width:108px;top:135px;height:17px;font-size:3.6px"><span>CONTINUE</span><span>»</span></div>
    <div class="foot" style="left:185px;right:0;top:233px">© 2024 HIRELUME. All rights reserved</div>
  </div>
</section>

<!-- 08 Email – Option Two -->
<section class="frame" style="left:419px;top:836px;width:363px;height:257px">
  <div class="toolbar"><i class="dot r"></i><i class="dot y"></i><i class="dot g"></i><span class="nav">‹ › ↻</span><svg width="6" height="6" viewBox="0 0 6 6"><circle cx="2.5" cy="2.5" r="1.8" fill="none" stroke="#ddd" stroke-width=".7"/><path d="M4 4l1.6 1.6" stroke="#ddd" stroke-width=".7"/></svg><span class="spacer"></span><span class="nav">☆ ≡</span></div>
  <div class="screen" style="background:#fff">
    <div class="photo" role="img" aria-label="Collage of office, resume and candidate photos" style="left:2px;top:2px;width:228px;height:232px;border-radius:3px;background:linear-gradient(150deg,#4B4E52 0%,#6C6F72 35%,#3A3D41 65%,#5A5D60 100%)"></div>
    <div class="quotecard" style="left:56px;top:72px;width:64px;height:82px"><div class="q">“</div><h5>Perfect CV platform</h5><p>Create, manage, and showcase your professional profile to land your dream job. Easy. Efficient. Effective.</p></div>
    <div class="brand" style="position:absolute;left:232px;right:0;top:88px;justify-content:center;font-size:13px"><i style="width:11px;height:11px"></i>HIRELUME</div>
    <div class="abs" style="left:232px;right:0;top:115px;text-align:center;font-size:4.2px;font-weight:500">Recruitment Web App Access</div>
    <div class="abs muted" style="left:232px;right:0;top:127px;text-align:center;font-size:3.4px">Type your email address in the box below</div>
    <div class="input" style="left:247px;width:101px;top:139px;height:14px;font-size:3.6px;color:var(--ink)"><svg width="5" height="5"><circle cx="2.5" cy="2.5" r="2" fill="none" stroke="#C2C6CB" stroke-width=".6"/></svg>alex.marren@mailbox.test</div>
    <div class="btn" style="left:247px;width:101px;top:158px;height:14px;font-size:3.6px"><span>CONTINUE</span><span>»</span></div>
    <div class="foot" style="left:232px;right:0;top:235px">© 2024 HIRELUME. All rights reserved</div>
  </div>
</section>

<!-- 09 One Time Password – Option Two -->
<section class="frame" style="left:812px;top:836px;width:363px;height:257px">
  <div class="toolbar"><i class="dot r"></i><i class="dot y"></i><i class="dot g"></i><span class="nav">‹ › ↻</span><svg width="6" height="6" viewBox="0 0 6 6"><circle cx="2.5" cy="2.5" r="1.8" fill="none" stroke="#ddd" stroke-width=".7"/><path d="M4 4l1.6 1.6" stroke="#ddd" stroke-width=".7"/></svg><span class="spacer"></span><span class="nav">☆ ≡</span></div>
  <div class="screen" style="background:#fff">
    <div class="photo" role="img" aria-label="Collage of office, resume and candidate photos" style="left:2px;top:2px;width:227px;height:232px;border-radius:3px;background:linear-gradient(150deg,#4B4E52 0%,#6C6F72 35%,#3A3D41 65%,#5A5D60 100%)"></div>
    <div class="quotecard" style="left:57px;top:70px;width:64px;height:82px"><div class="q">“</div><h5>Perfect CV platform</h5><p>Create, manage, and showcase your professional profile to land your dream job. Easy. Efficient. Effective.</p></div>
    <div class="brand" style="position:absolute;left:231px;right:0;top:85px;justify-content:center;font-size:13px"><i style="width:11px;height:11px"></i>HIRELUME</div>
    <div class="abs" style="left:231px;right:0;top:111px;text-align:center;font-size:4.2px;font-weight:500">Recruitment Web App Access</div>
    <div class="abs muted" style="left:231px;right:0;top:122px;text-align:center;font-size:3.4px">A one-time password has been sent to you</div>
    <div class="otpc on" style="left:246px;top:135px">9</div>
    <div class="otpc on" style="left:263px;top:135px">5</div>
    <div class="otpc on" style="left:280px;top:135px">7</div>
    <div class="otpc" style="left:297px;top:135px"></div>
    <div class="otpc" style="left:314px;top:135px"></div>
    <div class="otpc" style="left:331px;top:135px"></div>
    <div class="btn" style="left:246px;width:15px;top:157px;height:14px;font-size:5px;background:#6A6E71;justify-content:center">«</div>
    <div class="btn" style="left:264px;width:82px;top:157px;height:14px;font-size:3.6px;justify-content:center">CONTINUE</div>
    <div class="foot" style="left:231px;right:0;top:235px">© 2024 HIRELUME. All rights reserved</div>
  </div>
</section>

<div class="thanks">THANKS FOR WATCHING MY WORKS.</div>

</body>
</html>
```